New Webpage for High Class Expert Witness Services Company

We are looking for a minimalist design for a webpage that just has our logo and an entry form offer to connect with one of our Liaisons.
The entry form should just ask for Name, Email, Contact Info and Description of Project.

Company Name is: The Marlowe Crest Advisory Services

Number of Pages Required

1 page

```html
<!DOCTYPE html>
<html lang="en">
<head>
<meta charset="utf-8">
<title>The Marlowe Crest Advisory Services – Contact</title>
<link href="https://fonts.googleapis.com/css2?family=Cinzel:wght@600;700&family=Roboto:wght@400;500&display=swap" rel="stylesheet">
<style>
  :root {
    --stage: #cbcbcb;
    --bar: #121212;
    --bar-text: #f2f2f2;
    --ink: #141414;
    --muted: #5c5c5c;
    --light-bg-a: #ffffff;
    --light-bg-b: #e6e6e6;
    --dark-bg-a: #1c1c1c;
    --dark-bg-b: #080808;
    --card-light: rgba(255,255,255,0.72);
    --card-dark: rgba(6,6,6,0.85);
    --line-light: #dadada;
  }
  * { box-sizing: border-box; margin: 0; padding: 0; }
  html, body { width: 1200px; height: 568px; overflow: hidden; background: var(--stage); }
  body { position: relative; font-family: "Roboto", Arial, sans-serif; }

  .page {
    position: absolute; top: 53px; width: 532px; height: 463px; overflow: hidden;
    --fg: var(--ink); --sub: var(--muted);
  }
  .page--light { left: 48px; }
  .page--dark { left: 620px; --fg: #ffffff; --sub: #f0f0f0; }

  .page__backdrop { position: absolute; inset: 35px 0 40px 0; }
  .page--light .page__backdrop {
    background: radial-gradient(ellipse at 30% 60%, var(--light-bg-b), var(--light-bg-a) 70%);
  }
  .page--dark .page__backdrop {
    background: linear-gradient(160deg, var(--dark-bg-a) 0%, var(--dark-bg-b) 45%, #151515 75%, var(--dark-bg-b) 100%);
  }

  .masthead {
    position: absolute; top: 0; left: 0; right: 0; height: 35px; background: var(--bar);
    display: flex; align-items: center; justify-content: center; gap: 6px;
  }
  .brand-mark { width: 9px; height: 9px; background: var(--bar-text); }
  .brand-name {
    font-family: "Cinzel", Georgia, serif; font-weight: 600; font-size: 10px;
    color: var(--bar-text); letter-spacing: 0.3px; line-height: 1;
  }

  .hero { position: absolute; top: 72px; left: 0; right: 0; text-align: center; color: var(--fg); }
  .hero__title {
    font-family: "Cinzel", Georgia, serif; font-weight: 700; font-size: 24px; line-height: 26px;
  }
  .page--dark .hero__title { font-size: 19px; line-height: 21px; margin-top: 10px; }
  .hero__lead { margin-top: 7px; font-size: 9.3px; line-height: 10.6px; color: var(--sub); }
  .page--dark .hero__lead { margin-top: 4px; }

  .contact-card { position: absolute; left: 64px; top: 174px; width: 405px; height: 219px; }
  .page--light .contact-card { background: var(--card-light); border: 1px solid var(--line-light); }
  .page--dark .contact-card { background: var(--card-dark); }
  .contact-card__title {
    position: absolute; top: 23px; left: 0; right: 0; text-align: center;
    font-family: "Cinzel", Georgia, serif; font-weight: 700; font-size: 19px; color: var(--fg);
  }
  .contact-card__rule { position: absolute; top: 48px; left: 192px; width: 22px; height: 1.5px; background: #fff; }

  .field {
    position: absolute; height: 17px; border: 1px solid var(--fg); background: transparent;
    font-size: 6px; color: var(--sub); padding: 5px 0 0 8px;
  }
  .field--name { left: 27px; top: 62px; width: 113px; }
  .field--email { left: 146px; top: 62px; width: 113px; }
  .field--phone { left: 265px; top: 62px; width: 113px; }
  .field--message { left: 27px; top: 87px; width: 351px; height: 48px; }
  .page--dark .field { color: #fff; }

  .submit {
    position: absolute; left: 155px; top: 143px; width: 95px; height: 17px;
    font-size: 6px; font-weight: 500; text-align: center; line-height: 17px;
  }
  .page--light .submit { background: var(--bar); color: #fff; }
  .page--dark .submit { background: #e2e2e2; color: var(--ink); }

  .privacy-note {
    position: absolute; top: 174px; left: 27px; width: 351px; text-align: center;
    font-size: 6px; line-height: 10.7px; color: var(--sub);
  }

  .site-footer {
    position: absolute; left: 0; right: 0; bottom: 0; height: 40px;
    background: linear-gradient(90deg, #111 0%, #2a2a2a 50%, #111 100%);
    color: var(--bar-text); font-size: 7px; display: flex; align-items: center; justify-content: center;
  }
  .site-footer__code { position: absolute; right: 24px; font-size: 4.5px; }
</style>
</head>
<body>

<section class="page page--light">
  <div class="page__backdrop" role="img" aria-label="Soft light grey abstract geometric background"></div>
  <header class="masthead"><span class="brand-mark"></span><span class="brand-name">The Marlowe Crest Advisory Services</span></header>
  <div class="hero">
    <h1 class="hero__title">HIGH-CLASS EXPERT<br>WITNESS SERVICES</h1>
    <p class="hero__lead">Connect with one of our dedicated liaisons to discuss your case<br>with discretion and precision.</p>
  </div>
  <div class="contact-card">
    <h2 class="contact-card__title">CONTACT US</h2>
    <div class="field field--name">Name</div>
    <div class="field field--email">Email</div>
    <div class="field field--phone">Phone</div>
    <div class="field field--message">Message</div>
    <div class="submit">REQUEST CONSULTATION</div>
    <p class="privacy-note">Your information is strictly confidential and will only be used to connect you with the appropriate liaison. All inquiries are handled<br>with the highest level of discretion and professionalism.</p>
  </div>
  <footer class="site-footer">© The Marlowe Crest Advisory Services &nbsp;|&nbsp; All Rights Reserved<span class="site-footer__code">C38</span></footer>
</section>

<section class="page page--dark">
  <div class="page__backdrop" role="img" aria-label="Dark charcoal background with soft sweeping curves"></div>
  <header class="masthead"><span class="brand-mark"></span><span class="brand-name">The Marlowe Crest Advisory Services</span></header>
  <div class="hero">
    <h1 class="hero__title">HIGH-CLASS EXPERT<br>WITNESS SERVICES</h1>
    <p class="hero__lead">Connect with one of our dedicated liaisons to discuss your case<br>with discretion and precision.</p>
  </div>
  <div class="contact-card">
    <h2 class="contact-card__title">CONTACT US</h2>
    <span class="contact-card__rule"></span>
    <div class="field field--name">Name</div>
    <div class="field field--email">Email</div>
    <div class="field field--phone">Phone</div>
    <div class="field field--message">Message</div>
    <div class="submit">REQUEST CONSULTATION</div>
    <p class="privacy-note">Your information is strictly confidential and will only be used to connect you with the appropriate liaison. All inquiries are handled<br>with the highest level of discretion and professionalism.</p>
  </div>
  <footer class="site-footer">© The Marlowe Crest Advisory Services &nbsp;|&nbsp; All Rights Reserved<span class="site-footer__code">C38</span></footer>
</section>

</body>
</html>
```